VocaTerrana Community/ Talent Gallery

VocaTerrana is developing a collaborative career course, with coaching and community exchange. Goal is to offer a platform where talented candidates can show their expertise and find projects, partners, and develop their online portfolios!

Here is a good example of the type of thing we hope to create with focus on sustainability focused talent to task matching
http://www.brambleforth.com/global-themes/employment-and-growth/connecting-talent-with-opportunity-in-the-digital-age

We hope to have a "grid style" gallery where it is easy to search by talent types and focus areas within the scope of "Sustainability" issues...Food/Water/Energy, Public Health, Technology, Sustainable Cities, Infrastructure, Education, Policy, Emerging Economies, Ecosystems, Social Innovation, inclusive Security, Equity Issues. For each topic/ header we hope to have candidates post their completed portfolios to exhibit resumes, biography, a case study... they may actually prepare these on other sites, but can link in OR alternately that they can easily create here, similar to "pinqo.io" ....

Hope to include a blog space titled "Rising over the Rift", where people can mix it up across these topic issues as they are interdependent and often require partners across discipline areas! If possible another area where jobs related to these issues may be posted as project or job opportunities by potential employers.

If there is a way to create a feed from various job sites that already exist...like Jobora...or http://www.greenledgerworks.com/ that would be super great. Again...sort of a portal connection to bridge the gap ....instead of candidates having to search all the time, we are hoping they can advertise their talent and employers may search here for these well presented portfolios!

Target Market(s)

Educators, Students, Career Transitioners, Employers, Professional Associations, Talent Recruiters with focus on Sustainability related Talent to Task matching!

Industry/Entity Type

Sustainability

Number of Pages Required

4 page

Font styles to use
Sans Serif

Colors
3176b5
32b8a4
add136

Requirements
Must have
• Not sure about the coded/ uncoded option here....
• Must have - grid style area where Sustainability Professionals with varied focus areas can exhibit their talent portfolios
• appear as a Talent Gallery that starts with photos & obvious organization...other tabs to be in a menu.
• ability to search both talent and task opportunity areas to help coaches or community members make matches....some topic focused category or tag words to help make them searchable...???
• consistent professional styling to existing website and new artflock postcard shared in brief/ images area
• Interactive blog space where articles, issues may be posted, discussed
• Bulletin board or feed for project opportunities to be posted where candidates may locate them and/or employers may express specific "call" for talent..These may be Short term Internships, Projects, Consulting Team Opportunity, or Jobs/ part time to full time....
Nice to have
• A calendar area where we can post networking opportunities, issues presentations where potential partners can meet the next generation leaders, attend a forum or webinar presentation.
Should not have
• Too much text on front page...Should be clean design,

```html
<!DOCTYPE html>
<html lang="en">
<head>
<meta charset="utf-8">
<title>VocaTerrana</title>
<link href="https://fonts.googleapis.com/css2?family=Arimo:ital,wght@0,400;0,700;1,400&family=Open+Sans:wght@400;600&display=swap" rel="stylesheet">
<style>
:root{
  --blue:#3176b5;
  --blue-deep:#2c62a8;
  --teal:#32b8a4;
  --green:#add136;
  --green-btn:#8cc63f;
  --ink:#333;
  --muted:#666;
  --line:#e4e4e4;
  --dark:#1c1c1c;
  --darker:#111;
  --cal:#3a3f44;
}
*{margin:0;padding:0;box-sizing:border-box}
html,body{width:1200px;height:2782px;overflow:hidden}
body{font-family:"Arimo",Arial,sans-serif;color:var(--ink);background:#fff;position:relative}

/* hero */
.hero{position:absolute;left:0;top:0;width:1200px;height:655px;background:radial-gradient(ellipse at 50% 85%,#6f7d5e 0%,#48503f 35%,#2b2e29 75%,#1f211f 100%)}
.brand{position:absolute;left:98px;top:36px;display:flex;align-items:center;gap:12px;color:#fff;font-weight:700;font-size:22px;letter-spacing:.5px}
.brand-dot{width:42px;height:42px;border-radius:50%;background:var(--teal)}
.nav{position:absolute;right:98px;top:50px;display:flex;gap:18px;font-size:12.5px;color:#fff;text-transform:uppercase}
.nav .active{color:var(--teal)}
.hero h1{position:absolute;top:188px;width:100%;text-align:center;color:#fff;font-size:44px;font-weight:700;letter-spacing:1px}
.hero .tagline{position:absolute;top:248px;width:100%;text-align:center;color:#fff;font-size:17px}
.signup{position:absolute;left:139px;top:308px;width:920px;height:85px;background:rgba(90,90,90,.55);display:flex;align-items:center;padding-left:19px;gap:8px}
.field{width:268px;height:42px;background:#fff;display:flex;align-items:center;justify-content:space-between;padding:0 14px;font-size:12px;color:#444}
.field svg{width:13px;height:13px}
.go{width:50px;height:42px;background:var(--green-btn);display:flex;align-items:center;justify-content:center}
.slide-arrow{position:absolute;top:316px;width:42px;height:42px;border:2px solid rgba(255,255,255,.55);border-radius:50%;display:flex;align-items:center;justify-content:center}

/* features */
.features{position:absolute;left:98px;top:512px;width:1004px;height:278px;display:flex}
.feature{flex:1;color:#fff;text-align:center;padding-top:44px}
.feature.course{background:var(--blue-deep)}
.feature.coach{background:var(--teal)}
.feature.exchange{background:var(--green)}
.feature h3{font-weight:400;font-size:23px;margin-top:10px}
.feature p{font-size:11.5px;line-height:21px;margin:8px auto 0;width:290px}
.btn-ghost{display:inline-block;margin-top:18px;border:2px solid #fff;padding:8px 16px;font-size:13.5px;color:#fff}

/* welcome */
.section-title{position:absolute;width:100%;text-align:center;font-size:28px;font-weight:700;color:#333;letter-spacing:.3px}
.rule{position:absolute;left:568px;width:64px;height:3px;background:var(--green)}
.intro{position:absolute;top:910px;left:250px;width:700px;text-align:center;font-size:13px;line-height:22px;color:#555}
.topics{position:absolute;left:98px;top:978px;width:1004px;display:grid;grid-template-columns:repeat(4,1fr);grid-template-rows:214px 214px}
.topic{text-align:center;padding-top:8px;position:relative}
.topic:nth-child(-n+4){border-bottom:1px solid var(--line)}
.topic:not(:nth-child(4n))::after{content:"";position:absolute;right:0;top:10px;height:170px;width:1px;background:var(--line)}
.topic svg{width:42px;height:42px;stroke:#333;fill:none;stroke-width:1.6}
.topic h4{font-weight:400;font-size:18px;margin-top:10px;color:#222}
.topic p{font-size:11px;line-height:20px;color:#555;width:210px;margin:4px auto 0}
.tags{display:flex;justify-content:center;gap:6px;margin-top:16px}
.tags span{border:1px solid #ddd;font-size:10.5px;color:#999;padding:4px 10px}
.view-all-btn{position:absolute;left:501px;top:1404px;width:198px;height:44px;background:var(--green-btn);color:#fff;font-size:17px;display:flex;align-items:center;justify-content:center;border-radius:2px}

/* events */
.events{position:absolute;left:0;top:1503px;width:1200px;height:435px;background:radial-gradient(ellipse at 45% 60%,#3f80c2 0%,#3072b4 50%,#2a64a6 100%)}
.events h2{position:absolute;left:98px;top:50px;color:#fff;font-size:28px;font-weight:700}
.events .underline{position:absolute;left:98px;top:92px;width:60px;height:3px;background:var(--green)}
.post{position:absolute;left:98px;display:flex;gap:22px;color:#fff}
.post-date{width:60px;height:66px;background:var(--green);text-align:center;font-weight:700;font-size:17px;display:flex;flex-direction:column}
.post-date span{flex:1;display:flex;align-items:center;justify-content:center}
.post-date span:first-child{border-bottom:2px solid #fff}
.post h3{font-weight:400;font-size:20px;margin-top:2px}
.post p{font-size:13px;margin-top:4px}
.post em{display:block;font-size:11px;margin-top:6px;font-weight:700}
.btn-outline{position:absolute;left:98px;top:1855px;width:98px;height:44px;border:2px solid #fff;color:#fff;font-size:17px;display:flex;align-items:center;justify-content:center;border-radius:2px}
.calendar{position:absolute;left:614px;top:1567px;width:243px;height:307px;background:var(--cal);font-family:"Open Sans",Arial,sans-serif;color:#ddd}
.cal-head{height:56px;display:flex;align-items:center;justify-content:space-between;padding:0 22px 0 18px;color:#fff;font-weight:600;font-size:16px;border-bottom:2px solid #555;margin:0 6px}
.circ{width:17px;height:17px;border:1.5px solid #ddd;border-radius:50%;display:flex;align-items:center;justify-content:center}
.cal-grid{display:grid;grid-template-columns:repeat(7,1fr);padding:10px 10px 0;font-size:12.5px;text-align:center}
.cal-grid span{height:30px;line-height:30px}
.cal-grid .dow{color:#eee;font-size:12px}
.cal-grid .we{color:var(--green)}
.cal-grid .dim{color:#aaa}
.cal-grid .today{background:#5a6a3a;color:#fff}
.day-card{position:absolute;left:857px;top:1567px;width:247px;height:307px;background:var(--green);color:#fff;text-align:center;font-family:"Open Sans",Arial,sans-serif}
.day-card .dow-big{margin-top:30px;font-size:20px;letter-spacing:.5px}
.day-card .num{font-size:104px;font-weight:400;line-height:1;margin-top:34px}
.day-card .foot{position:absolute;bottom:0;left:0;right:0;height:46px;border-top:1px solid rgba(255,255,255,.6);display:flex;align-items:center;justify-content:center;gap:10px;font-size:15px}
.day-card .gear{position:absolute;right:10px;top:12px}
.day-card .circ{border-color:#fff}

/* articles */
.articles{position:absolute;left:0;top:1938px;width:1200px;height:581px;background:linear-gradient(135deg,#f4f4f4,#e9e9e9 50%,#f2f2f2)}
.card{position:absolute;top:141px;width:306px;height:373px;background:#fff;box-shadow:0 1px 3px rgba(0,0,0,.08)}
.card .photo{height:184px}
.card .source{font-size:11px;color:#666;padding:10px 16px 0}
.card .rowt{display:flex;gap:12px;padding:14px 16px 0}
.card .dt{width:32px;flex:none;text-align:center;border:1px solid #ccd}
.card .dt b{display:block;background:var(--blue-deep);color:#fff;font-size:15px;line-height:24px}
.card .dt i{display:block;font-style:normal;font-size:10px;color:var(--blue-deep);line-height:16px}
.card h4{font-weight:400;font-size:16px;color:#1f3a60;line-height:21px;text-transform:uppercase}
.card .by{font-size:11px;color:#555;font-style:italic;margin-top:2px}
.card .by b{font-weight:700}
.card .ex{font-size:11.5px;line-height:21px;color:#555;padding:12px 16px 0;text-align:justify}

/* footer */
.footer{position:absolute;left:0;top:2519px;width:1200px;height:201px;background:var(--dark);color:#fff}
.fcol{position:absolute;top:44px}
.fcol h5{font-weight:400;font-size:17px;margin-bottom:14px}
.fcol li{list-style:none;font-size:11.5px;color:#aaa;line-height:21px}
.news-input{width:210px;height:40px;background:#2a2a2a;color:#777;font-size:11px;padding:13px 10px}
.send{position:absolute;left:128px;top:106px;width:82px;height:28px;background:var(--green-btn);color:#fff;font-size:12px;display:flex;align-items:center;justify-content:center;border-radius:2px}
.bottom{position:absolute;left:0;top:2720px;width:1200px;height:62px;background:var(--darker);color:#ccc;font-size:12px;text-align:center;line-height:62px}
</style>
</head>
<body>

<header class="hero" role="img" aria-label="Hands cupping a young seedling in soil">
  <div class="brand"><span class="brand-dot"></span>VOCATERRANA</div>
  <nav class="nav"><span class="active">Home</span><span>About</span><span>Portfolios</span><span>Positions</span><span>Projects</span><span>Perspectives</span><span>Partners</span><span>Log in</span></nav>
  <h1>VOCATERRANA</h1>
  <p class="tagline">We are creating a collaborative career course,with coaching and community exchange.</p>
  <div class="signup">
    <div class="field">Name<svg viewBox="0 0 14 14" fill="#555"><circle cx="7" cy="4" r="3"/><path d="M1 14c0-4 3-6 6-6s6 2 6 6z"/></svg></div>
    <div class="field">Mail Id<svg viewBox="0 0 14 14" fill="none" stroke="#555" stroke-width="1.4"><rect x="1" y="3" width="12" height="8"/><path d="M1 3l6 5 6-5"/></svg></div>
    <div class="field">Upload Resume<svg viewBox="0 0 14 14" fill="#555"><path d="M7 1l4 4H8.5v4h-3V5H3z"/><rect x="1" y="11" width="12" height="2"/></svg></div>
    <div class="go"><svg width="20" height="20" viewBox="0 0 20 20" fill="none" stroke="#fff" stroke-width="2.6"><circle cx="8" cy="8" r="5.5"/><path d="M12 12l6 6"/></svg></div>
  </div>
  <div class="slide-arrow" style="left:35px"><svg width="14" height="14" viewBox="0 0 14 14" fill="none" stroke="#fff" stroke-width="2"><path d="M9 2L4 7l5 5"/></svg></div>
  <div class="slide-arrow" style="left:1120px"><svg width="14" height="14" viewBox="0 0 14 14" fill="none" stroke="#fff" stroke-width="2"><path d="M5 2l5 5-5 5"/></svg></div>
</header>

<section class="features">
  <div class="feature course">
    <svg width="40" height="44" viewBox="0 0 40 44" fill="#fff"><circle cx="20" cy="10" r="8"/><path d="M4 42c0-12 7-18 16-18s16 6 16 18z"/><path d="M18 24h4l-1 14h-2z" fill="#2c62a8"/></svg>
    <h3>CAREER COURSE</h3>
    <p>Our mission is to cultivate a community of learning and professional practice to support career</p>
    <span class="btn-ghost">Read More</span>
  </div>
  <div class="feature coach">
    <svg width="44" height="44" viewBox="0 0 44 44" fill="none" stroke="#fff" stroke-width="2"><rect x="6" y="6" width="32" height="22"/><path d="M12 22l7-7 5 4 8-8M22 28v6M14 42l8-8 8 8M3 6h38"/></svg>
    <h3>COACHING</h3>
    <p>Our mission is to cultivate a community of learning and professional practice to support career</p>
    <span class="btn-ghost">Read More</span>
  </div>
  <div class="feature exchange">
    <svg width="44" height="44" viewBox="0 0 44 44" fill="none" stroke="#fff" stroke-width="2.2"><circle cx="17" cy="24" r="12"/><path d="M24 8a12 12 0 0 1 16 12"/><path d="M20 19h-5a2.5 2.5 0 0 0 0 5h4a2.5 2.5 0 0 1 0 5h-5M17 16v3M17 29v3"/></svg>
    <h3>COMMUNITY EXCHANGE</h3>
    <p>Our mission is to cultivate a community of learning and professional practice to support career</p>
    <span class="btn-ghost">Read More</span>
  </div>
</section>

<h2 class="section-title" style="top:838px">WELCOME TO VOCATERRANA</h2>
<div class="rule" style="top:884px"></div>
<p class="intro">Our mission is to cultivate a community of learning and professional practice to support career transitions and next generation leadership of sustainable solutions that balance economic, environment, and equity</p>

<section class="topics">
  <div class="topic"><svg viewBox="0 0 42 42"><path d="M13 10a14 14 0 1 0 16 0"/><path d="M21 4v16"/></svg><h4>ENERGY</h4><p>Our mission is to cultivate a community of learning and professional</p><div class="tags"><span>Talent</span><span>Projects</span><span>Job Postings</span></div></div>
  <div class="topic"><svg viewBox="0 0 42 42"><path d="M21 22c-6-5-10-8-10-12a5 5 0 0 1 10-1 5 5 0 0 1 10 1c0 4-4 7-10 12z"/><path d="M4 20c2 8 8 14 17 16 9-2 15-8 17-16"/></svg><h4>PUBLIC HEALTH</h4><p>Our mission is to cultivate a community of learning and professional</p><div class="tags"><span>Talent</span><span>Projects</span><span>Job Postings</span></div></div>
  <div class="topic"><svg viewBox="0 0 42 42"><rect x="4" y="6" width="34" height="24" rx="1"/><path d="M4 25h34M17 30l-2 6M25 30l2 6M12 36h18"/></svg><h4>TECHNOLOGY</h4><p>Our mission is to cultivate a community of learning and professional</p><div class="tags"><span>Talent</span><span>Projects</span><span>Job Postings</span></div></div>
  <div class="topic"><svg viewBox="0 0 42 42"><path d="M4 38h34M7 38V22h8v16M15 38V10h10v28M25 38V16h9v22M19 14h2M19 20h2M19 26h2M28 20h3M28 26h3"/></svg><h4>SUSTAINABLE CITIES</h4><p>Our mission is to cultivate a community of learning and professional</p><div class="tags"><span>Talent</span><span>Projects</span><span>Job Postings</span></div></div>
  <div class="topic"><svg viewBox="0 0 42 42"><path d="M2 16l19-8 19 8-19 8z"/><path d="M10 20v10c4 4 18 4 22 0V20M37 17v12"/></svg><h4>EDUCATION</h4><p>Our mission is to cultivate a community of learning and professional</p><div class="tags"><span>Talent</span><span>Projects</span><span>Job Postings</span></div></div>
  <div class="topic"><svg viewBox="0 0 42 42"><circle cx="17" cy="24" r="12"/><path d="M24 8a12 12 0 0 1 14 14"/><path d="M20 19h-5a2.5 2.5 0 0 0 0 5h4a2.5 2.5 0 0 1 0 5h-5M17 16v3M17 29v3"/></svg><h4>COMMUNITY</h4><p>Our mission is to cultivate a community of learning and professional</p><div class="tags"><span>Talent</span><span>Projects</span><span>Job Postings</span></div></div>
  <div class="topic"><svg viewBox="0 0 42 42"><path d="M21 4c10 8 10 26 0 34-10-8-10-26 0-34z"/><path d="M21 10v28M13 12c-8 6-6 20 4 24M29 12c8 6 6 20-4 24"/></svg><h4>ECOSYSTEMS</h4><p>Our mission is to cultivate a community of learning and professional</p><div class="tags"><span>Talent</span><span>Projects</span><span>Job Postings</span></div></div>
  <div class="topic"><svg viewBox="0 0 42 42"><circle cx="30" cy="9" r="5"/><circle cx="10" cy="21" r="5"/><circle cx="30" cy="33" r="5"/><path d="M14 19l12-7M14 23l12 7"/></svg><h4>SOCIAL INNOVATION</h4><p>Our mission is to cultivate a community of learning and professional</p><div class="tags"><span>Talent</span><span>Projects</span><span>Job Postings</span></div></div>
</section>
<div class="view-all-btn">Click Here To View All</div>

<section class="events" role="img" aria-label="Faint world map over blue background">
  <h2>LATEST POST</h2>
  <div class="underline"></div>
  <div class="post" style="top:125px"><div class="post-date"><span>June</span><span>21</span></div><div><h3>NETWORKING OPPORTUNITIES</h3><p>Through a proven four-phase process, integrating</p><em>Posted By Marla Quenby / June 21, 2016</em></div></div>
  <div class="post" style="top:222px"><div class="post-date"><span>June</span><span>21</span></div><div><h3>NETWORKING OPPORTUNITIES</h3><p>Through a proven four-phase process, integrating</p><em>Posted By Marla Quenby / June 21, 2016</em></div></div>
</section>
<div class="btn-outline">View All</div>

<div class="calendar">
  <div class="cal-head"><span class="circ"><svg width="7" height="8" viewBox="0 0 7 8" fill="#ddd"><path d="M6 0v8L0 4z"/></svg></span>JUNE 2016<span class="circ"><svg width="7" height="8" viewBox="0 0 7 8" fill="#ddd"><path d="M1 0v8l6-4z"/></svg></span></div>
  <div class="cal-grid">
    <span class="dow we">SU</span><span class="dow">MO</span><span class="dow">TU</span><span class="dow">WE</span><span class="dow">TH</span><span class="dow">FR</span><span class="dow we">SA</span>
    <span class="dim">28</span><span class="dim">29</span><span class="dim">30</span><span>1</span><span>2</span><span>3</span><span>4</span>
    <span>5</span><span>6</span><span>7</span><span>8</span><span>9</span><span>10</span><span>11</span>
    <span>12</span><span>13</span><span>14</span><span>15</span><span>16</span><span>17</span><span>18</span>
    <span>19</span><span class="today">20</span><span>21</span><span>22</span><span>23</span><span>24</span><span>25</span>
    <span>26</span><span>27</span><span>28</span><span>29</span><span>30</span><span>31</span><span class="dim">1</span>
    <span class="dim">2</span><span class="dim">3</span><span class="dim">4</span><span class="dim">5</span><span class="dim">6</span><span class="dim">7</span><span class="dim">8</span>
  </div>
</div>
<div class="day-card">
  <svg class="gear" width="18" height="18" viewBox="0 0 18 18"><circle cx="9" cy="9" r="5.5" fill="none" stroke="#fff" stroke-width="3"/><path d="M9 0v4M9 14v4M0 9h4M14 9h4M2.6 2.6l2.8 2.8M12.6 12.6l2.8 2.8M2.6 15.4l2.8-2.8M12.6 5.4l2.8-2.8" stroke="#fff" stroke-width="3"/></svg>
  <div class="dow-big">TUESDAY</div>
  <div class="num">21</div>
  <div class="foot"><span class="circ"><svg width="7" height="8" viewBox="0 0 7 8" fill="#fff"><path d="M6 0v8L0 4z"/></svg></span>JUNE 2014<span class="circ"><svg width="7" height="8" viewBox="0 0 7 8" fill="#fff"><path d="M1 0v8l6-4z"/></svg></span></div>
</div>

<section class="articles">
  <h2 class="section-title" style="top:56px">RISING OVER THE RIFT</h2>
  <div class="rule" style="top:100px"></div>
  <article class="card" style="left:98px">
    <div class="photo" role="img" aria-label="Group photo of workshop participants outdoors" style="background:linear-gradient(180deg,#6b8a5a,#8a7a6a 60%,#5f7a4a)"></div>
    <div class="source">Book Excerpt - Brambleforth Global Institute</div>
    <div class="rowt"><div class="dt"><b>21</b><i>June</i></div><div><h4>Ecosystem Insights for Leaders</h4><div class="by">April 8, 2016 by <b>Odette Varnell</b></div></div></div>
    <p class="ex">As an offering for leaders engaged in systems change, we offer seven important lessons from our work with thousands of educators.</p>
  </article>
  <article class="card" style="left:447px">
    <div class="photo" role="img" aria-label="Three professionals posing at an event" style="background:linear-gradient(180deg,#6a4a3a,#3a3030 55%,#2a2a2e)"></div>
    <div class="source">Book Excerpt - Brambleforth Global Institute</div>
    <div class="rowt"><div class="dt"><b>22</b><i>June</i></div><div><h4>Sustainable in the Deve- lopment ?</h4><div class="by">February 8, 2016 by <b>Odette Varnell</b></div></div></div>
    <p class="ex">Rowan Elsby has recently published his book, The Balanced Horizon Handbook, which offers a helpful synthesis of data, insights</p>
  </article>
  <article class="card" style="left:796px">
    <div class="photo" role="img" aria-label="Panel discussion at a conference table" style="background:linear-gradient(180deg,#4a4a55,#6a6a78 50%,#3a3a44)"></div>
    <div class="source">Book Excerpt - Brambleforth Global Institute</div>
    <div class="rowt"><div class="dt"><b>23</b><i>June</i></div><div><h4>What Does Sustainability Mean to You?</h4><div class="by">February 6, 2016 by <b>Odette Varnell</b></div></div></div>
    <p class="ex">What does Sustainability mean to you? The word is used everywhere nowadays, across business, government, education, and non-profits.</p>
  </article>
</section>

<footer class="footer">
  <div class="fcol" style="left:102px"><h5>COMPANY</h5><ul><li>Home</li><li>About us</li><li>Services</li><li>Contact us</li></ul></div>
  <div class="fcol" style="left:265px"><h5>COMMUNITY</h5><ul><li>Guiglines</li><li>Terms and conditions</li><li>privacy policy</li><li>site map</li></ul></div>
  <div class="fcol" style="left:462px"><h5>FOLLOW US</h5><ul><li>Friendloop</li><li>Chirpline</li><li>Snapgrid</li><li>Searchly</li></ul></div>
  <div class="fcol" style="left:638px;width:220px"><h5>CONTACT US</h5><ul><li>Address : 200 Latin words, combined with a handful</li><li>Ph : 5550142288 / 5550142288</li><li>E mail : info@vocaterrana.org</li></ul></div>
  <div class="fcol" style="left:892px"><h5>NEWSLETTER</h5><div class="news-input">Enter The mail id</div><div class="send">Send Now</div></div>
</footer>
<div class="bottom">Copyrights@2016Company name all rights reserved</div>

</body>
</html>
```